Fernhale Business Card Design

We are looking for a fresh business card design for our new logo. We would like a business card that is unique but friendly. We are in the window coverings business offering blinds, shutters and shades for homes.

Target Market(s)

Targeting the end-consumer

Industry/Entity Type

Business

Requirements
Must have
• Must have a dedicates space for a photo of our sales person. Must contain our new logo (attached).

```html
<!DOCTYPE html>
<html lang="en">
<head>
<meta charset="utf-8">
<title>Fernhale Business Card</title>
<link rel="stylesheet" href="https://fonts.googleapis.com/css2?family=Roboto:wght@400;500&family=Open+Sans:wght@400&display=swap">
<style>
  :root {
    --backdrop: #e9e6e1;
    --card-white: #fbfbfa;
    --card-grey: #78787c;
    --ink: #555558;
    --ink-soft: #88888b;
    --leaf-green: #7cc242;
    --rule: #8a8a8d;
    --photo-tone: #c9c9cb;
  }
  html, body {
    margin: 0;
    padding: 0;
    overflow: hidden;
  }
  body {
    width: 1200px;
    height: 886px;
    background: var(--backdrop);
    display: flex;
    align-items: center;
    justify-content: center;
    gap: 40px;
    font-family: "Roboto", Arial, sans-serif;
  }
  .card {
    width: 540px;
    height: 310px;
    position: relative;
    box-shadow: 0 6px 18px rgba(0,0,0,0.18);
    box-sizing: border-box;
  }
  .card-front { background: var(--card-white); }
  .card-back { background: var(--card-grey); }

  .brand {
    display: flex;
    align-items: center;
    gap: 12px;
    font-family: "Open Sans", Arial, sans-serif;
    font-weight: 400;
  }
  .brand-mark {
    background: var(--leaf-green);
    display: block;
  }

  .card-front .brand {
    position: absolute;
    left: 230px;
    top: 52px;
    color: var(--ink-soft);
    font-size: 40px;
    letter-spacing: 1px;
  }
  .card-front .brand-mark { width: 26px; height: 26px; }

  .photo-slot {
    position: absolute;
    left: 22px;
    top: 22px;
    width: 150px;
    height: 118px;
    border-radius: 10px;
    border: 2px solid #7e7e80;
    background: linear-gradient(180deg, var(--photo-tone), #a9a9ab);
    box-sizing: border-box;
  }
  .divider {
    position: absolute;
    left: 190px;
    right: 0;
    top: 150px;
    height: 1px;
    background: var(--rule);
  }
  .person {
    position: absolute;
    left: 22px;
    top: 160px;
  }
  .person-name {
    margin: 0;
    color: var(--leaf-green);
    font-size: 20px;
    font-weight: 500;
    letter-spacing: 0.5px;
  }
  .person-title {
    margin: 2px 0 0;
    color: var(--ink);
    font-size: 14px;
    padding-bottom: 8px;
    border-bottom: 1px solid var(--rule);
    width: 96px;
  }
  .contact-list {
    list-style: none;
    margin: 10px 0 0;
    padding: 0;
    color: var(--ink);
    font-size: 13.5px;
    line-height: 20px;
  }
  .contact-list li {
    display: flex;
    align-items: center;
    gap: 8px;
  }
  .contact-list svg { width: 12px; height: 12px; flex: none; }

  .address {
    position: absolute;
    right: 24px;
    top: 168px;
    text-align: right;
    color: var(--ink);
    font-size: 14px;
    line-height: 20px;
    margin: 0;
    font-style: normal;
  }

  .card-back .brand {
    position: absolute;
    left: 70px;
    top: 110px;
    color: #ffffff;
    font-size: 62px;
    letter-spacing: 1px;
  }
  .card-back .brand-mark { width: 40px; height: 40px; }
  .card-back .web {
    position: absolute;
    left: 122px;
    top: 200px;
    color: #e4e4e6;
    font-size: 12px;
    letter-spacing: 4px;
    margin: 0;
  }
</style>
</head>
<body>
  <section class="card card-front" aria-label="Business card front">
    <div class="photo-slot" role="img" aria-label="Photo of the sales person"></div>
    <div class="brand">
      <span class="brand-mark"></span>
      <span class="brand-name">Fernhale</span>
    </div>
    <div class="divider"></div>

    <div class="person">
      <p class="person-name">DANA MERCER</p>
      <p class="person-title">CEO/FOUNDER</p>
      <ul class="contact-list">
        <li>
          <svg viewBox="0 0 12 12" aria-hidden="true"><path d="M2 1h3l1 3-1.5 1a7 7 0 0 0 2.5 2.5L8 6l3 1v3c0 .6-.4 1-1 1A9 9 0 0 1 1 2c0-.6.4-1 1-1z" fill="var(--leaf-green)"/></svg>
          555 210 4418
        </li>
        <li>
          <svg viewBox="0 0 12 12" aria-hidden="true"><rect x="3" y="0.5" width="6" height="11" rx="1.2" fill="none" stroke="var(--leaf-green)" stroke-width="1.2"/></svg>
          555 731 2906
        </li>
        <li>
          <svg viewBox="0 0 12 12" aria-hidden="true"><rect x="1" y="4" width="10" height="7" rx="1" fill="var(--leaf-green)"/><rect x="3" y="1" width="6" height="4" fill="none" stroke="var(--leaf-green)"/></svg>
          555 864 0153
        </li>
        <li>
          <svg viewBox="0 0 12 12" aria-hidden="true"><rect x="0.5" y="2" width="11" height="8" fill="var(--leaf-green)"/><path d="M1 2.5 6 7l5-4.5" fill="none" stroke="#fff" stroke-width="1"/></svg>
          hello@fernhale.com
        </li>
      </ul>
    </div>

    <address class="address">
      4120 Willowmere Road<br>
      Brookfield, Oregon 97512<br>
      www.fernhale.com
    </address>
  </section>

  <section class="card card-back" aria-label="Business card back">
    <div class="brand">
      <span class="brand-mark"></span>
      <span class="brand-name">Fernhale</span>
    </div>
    <p class="web">www.fernhale.com</p>
  </section>
</body>
</html>
```